Building company buisness cards

We are looking for a sharp modern new look for our business cards.
We are a New Zealand based company that specialises in house and land packages.
We have attached a photo of the current logo and would like to see if it can be improved somehow if needed.
We are open to any colours but we have chosen green at this stage.
Feel free to change the font and make the logo smarter looking.
Play with the colours and see what looks best.

We want a card that looks so good know one will want to throw it away!

Target Market(s)

Home buyers

Industry/Entity Type

Building

Contact Information for Business Card

Derek Tolvane
0217394062
dtolvane@quillmarkhomesteads.co.nz
quillmarkhomesteads.co.nz

Font styles to use
Serif
Sans Serif

Colors

Designer to choose colors to be used in the design.

Requirements
Must have
• Logo and company name on one side, details on the other side
Nice to have
• Color codes for the original green are HEX #4a8028, RGB(74,128,40), CMYK(42,0,69,50)
• Round corners, Raised and/or spot UV

```html
<!DOCTYPE html>
<html lang="en">
<head>
<meta charset="utf-8">
<title>Quillmark Homesteads – Business Cards</title>
<link rel="stylesheet" href="https://fonts.googleapis.com/css2?family=Open+Sans:wght@400;800&display=swap">
<style>
  :root {
    --backdrop: #3b3b3c;
    --card: #ffffff;
    --brand-green: #1f9a24;
    --rule-grey: #4b4b4d;
    --ink: #2a2a2a;
  }
  * { box-sizing: border-box; margin: 0; padding: 0; }
  html, body {
    width: 1200px;
    height: 716px;
    overflow: hidden;
  }
  body {
    background: var(--backdrop);
    font-family: "Open Sans", Arial, sans-serif;
    position: relative;
  }
  .card {
    position: absolute;
    width: 525px;
    height: 300px;
    background: var(--card);
    border-radius: 6px;
    overflow: hidden;
  }
  .card--front { left: 50px; top: 208px; }
  .card--back  { left: 625px; top: 208px; }

  .rule {
    position: absolute;
    left: 0;
    right: 0;
    height: 5px;
    display: flex;
  }
  .rule__green { width: 46%; background: var(--brand-green); }
  .rule__grey  { flex: 1; background: var(--rule-grey); }
  .card--front .rule { top: 128px; }
  .card--back  .rule { top: 150px; }

  .brand {
    position: absolute;
    display: flex;
    align-items: center;
    gap: 8px;
    color: var(--brand-green);
    font-weight: 800;
    font-size: 25px;
    letter-spacing: -0.3px;
    white-space: nowrap;
  }
  .brand__mark {
    width: 14px;
    height: 14px;
    background: var(--brand-green);
    flex: none;
  }
  .card--front .brand { left: 50%; top: 58px; transform: translateX(-50%); }
  .card--back  .brand { left: 58%; top: 82px; transform: translateX(-50%); }

  .contacts {
    position: absolute;
    left: 26px;
    top: 176px;
    list-style: none;
    font-size: 12.5px;
    color: var(--ink);
    line-height: 1;
  }
  .contacts li {
    display: flex;
    align-items: center;
    gap: 9px;
    margin-bottom: 7px;
  }
  .contacts svg { width: 11px; height: 11px; flex: none; }

  .holder-name {
    position: absolute;
    right: 48px;
    bottom: 46px;
    color: var(--brand-green);
    font-size: 19px;
    font-weight: 400;
  }
</style>
</head>
<body>

  <section class="card card--front" aria-label="Card front">
    <div class="brand"><span class="brand__mark"></span>quillmark homesteads.</div>
    <div class="rule"><span class="rule__green"></span><span class="rule__grey"></span></div>
  </section>

  <section class="card card--back" aria-label="Card back">
    <div class="brand"><span class="brand__mark"></span>quillmark homesteads.</div>
    <div class="rule"><span class="rule__green"></span><span class="rule__grey"></span></div>

    <ul class="contacts">
      <li>
        <svg viewBox="0 0 11 11" aria-hidden="true"><rect width="11" height="11" rx="1.5" fill="#1f9a24"/><path d="M3.2 2.4l1.3 1.6-.7.8c.4.9 1 1.5 1.9 1.9l.8-.7 1.6 1.3-.7 1.1C5.3 8.3 2.7 5.7 2.1 3.1z" fill="#fff"/></svg>
        0217394062
      </li>
      <li>
        <svg viewBox="0 0 11 11" aria-hidden="true"><rect width="11" height="11" rx="1.5" fill="#1f9a24"/><rect x="2.2" y="3.2" width="6.6" height="4.6" fill="none" stroke="#fff" stroke-width="0.9"/><path d="M2.2 3.3l3.3 2.5 3.3-2.5" fill="none" stroke="#fff" stroke-width="0.9"/></svg>
        dtolvane@quillmarkhomesteads.co.nz
      </li>
      <li>
        <svg viewBox="0 0 11 11" aria-hidden="true"><rect width="11" height="11" rx="1.5" fill="#1f9a24"/><circle cx="5.5" cy="5.5" r="3.2" fill="none" stroke="#fff" stroke-width="0.9"/><path d="M2.3 5.5h6.4M5.5 2.3c-1.4 1.8-1.4 4.6 0 6.4M5.5 2.3c1.4 1.8 1.4 4.6 0 6.4" fill="none" stroke="#fff" stroke-width="0.7"/></svg>
        quillmarkhomesteads.co.nz
      </li>
    </ul>

    <p class="holder-name">Derek Tolvane</p>
  </section>

</body>
</html>
```